Business Cards Design for the electrical wholesaler: clean bold dynamic :)

We need a business card design that would follow our latest brand guidelines. As an electrical wholesaler we want to bring a fresh look and feel into the industry. The design should be clean bold and dynamic. It should come alive with the renewed energy of our green colour. Our grey colour should keep things balanced and complement the notion of maturity and responsibility. We employ Lato as a corporate font however are not bound by this font and we’re open to interpretation here.

Target Market(s)

Electrical contractors

Industry/Entity Type

Business

Contact Information for Business Card

Logo
Name & Surname: Halyna Dorosh
Job Title: Director of Marketing
Email: halya.dorosh@quillmail.example
Cell phone: XXX.XXX.XXXX
Address: 20517 - 87 Ave. Edmonton, AB, Canada. T6K 4N8
Business Phone: 780.555.0184
Website: www.brovix.example

Font styles to use
Other font styles liked:
• Lato

Requirements
Must have
• Logo & website
Nice to have
• Brand elements - some of them you may find in the attached Brand Guidelines (e.g. three lines on the background signifying "W")

```html
<!DOCTYPE html>
<html lang="en">
<head>
<meta charset="utf-8">
<title>Brovix Business Card</title>
<link href="https://fonts.googleapis.com/css2?family=Lato:ital,wght@0,300;0,400;0,700;1,400&display=swap" rel="stylesheet">
<style>
  :root {
    --bg: #2b2b2b;
    --card: #141414;
    --card-edge: #1e1e1e;
    --green: #8dc63f;
    --green-dark: #6fa52a;
    --grey: #b5b5b5;
    --white: #f4f4f4;
  }
  * { margin: 0; padding: 0; box-sizing: border-box; }
  html, body {
    width: 800px; height: 1200px; overflow: hidden;
    background: var(--bg);
    font-family: "Lato", sans-serif;
  }
  .stage {
    width: 800px; height: 1200px;
    display: flex; flex-direction: column;
    justify-content: center; align-items: center; gap: 100px;
  }
  .card {
    position: relative;
    width: 680px; height: 400px;
    border-radius: 28px;
    background: linear-gradient(160deg, var(--card-edge), var(--card));
    overflow: hidden;
  }
  .brand {
    display: flex; align-items: center; gap: 14px;
    color: var(--white);
    font-weight: 400;
    letter-spacing: 1px;
  }
  .brand-mark {
    width: 0.62em; height: 0.62em;
    background: var(--green);
  }
  .card-front .brand {
    position: absolute; left: 50%; top: 50%;
    transform: translate(-50%, -50%);
    font-size: 92px;
  }
  .card-back .brand {
    position: absolute; left: 40px; top: 36px;
    font-size: 60px;
  }
  .person {
    position: absolute; left: 44px; top: 128px;
  }
  .person-name {
    color: var(--green);
    font-style: italic;
    font-size: 32px;
    font-weight: 400;
  }
  .person-title {
    color: var(--grey);
    font-size: 16px;
    margin-top: 4px;
  }
  .wave { position: absolute; left: 0; bottom: 0; width: 680px; height: 240px; }
  .contact {
    position: absolute; right: 36px; bottom: 36px;
    list-style: none;
    text-align: right;
    color: var(--white);
    font-size: 15px;
    line-height: 1.6;
  }
  .contact li { display: flex; justify-content: flex-end; align-items: center; gap: 10px; }
  .contact .icon { width: 12px; height: 12px; flex: none; }
  .contact .spacer { width: 12px; flex: none; }
</style>
</head>
<body>
<main class="stage">
  <section class="card card-front" aria-label="Business card front">
    <div class="brand"><span class="brand-mark"></span><span>brovix</span></div>
  </section>

  <section class="card card-back" aria-label="Business card back">
    <div class="brand"><span class="brand-mark"></span><span>brovix</span></div>
    <div class="person">
      <h1 class="person-name">Halyna Dorosh</h1>
      <p class="person-title">Director of Marketing</p>
    </div>
    <svg class="wave" viewBox="0 0 680 240" preserveAspectRatio="none" aria-hidden="true">
      <path d="M0 78 C180 66 300 192 480 224 C560 238 620 238 680 232 L680 240 L0 240 Z" fill="var(--green)"/>
      <path d="M0 118 C170 110 280 212 420 240 L0 240 Z" fill="var(--card)"/>
      <path d="M0 108 C170 100 282 204 424 240" fill="none" stroke="var(--grey)" stroke-width="5"/>
      <path d="M0 166 C90 168 150 204 186 240 L0 240 Z" fill="var(--green-dark)"/>
    </svg>
    <ul class="contact">
      <li><span>www.brovix.example</span><svg class="icon" viewBox="0 0 12 12"><circle cx="6" cy="6" r="5" fill="none" stroke="var(--green)" stroke-width="1.5"/><path d="M1 6h10M6 1c-2 3-2 7 0 10M6 1c2 3 2 7 0 10" fill="none" stroke="var(--green)" stroke-width="1"/></svg></li>
      <li><span>halya.dorosh@quillmail.example</span><svg class="icon" viewBox="0 0 12 12"><rect x="0.5" y="2" width="11" height="8" fill="none" stroke="var(--green)" stroke-width="1.4"/><path d="M1 2.5l5 4 5-4" fill="none" stroke="var(--green)" stroke-width="1.2"/></svg></li>
      <li><span>+1 780.555.0184</span><svg class="icon" viewBox="0 0 12 12"><path d="M2 1l2.5 0 1 3-1.5 1c.7 1.4 1.6 2.3 3 3l1-1.5 3 1V11C5 11 1 7 1 2z" fill="var(--green)"/></svg></li>
      <li><span>20517 - 87 Ave. Edmonton</span><svg class="icon" viewBox="0 0 12 12"><path d="M6 11.5C3 8 2 6 2 4.5a4 4 0 0 1 8 0C10 6 9 8 6 11.5z" fill="var(--green)"/><circle cx="6" cy="4.5" r="1.4" fill="var(--card)"/></svg></li>
      <li><span>AB, Canada T6K 4N8</span><span class="spacer"></span></li>
    </ul>
  </section>
</main>
</body>
</html>
```